LHP Letterhead

I need letterhead for "maple crest holdings llc" ...

logo attached to project..

Company Info:
815 East Darrow Avenue, Suite 4B
Chicago, Illinois 60417
ofc 312-555-0148
facsimile 312-555-0192
www.maplecrestholdingsllc.example
info@maplecrestholdingsllc.example

I have multiple projects listed.. see below:

Business cards for maple crest holdings llc
letterhead "
envelopes "

Business cards for KP Exchange LLC
letterhead "
envelopes "

Industry/Entity Type

It Company

```html
<!DOCTYPE html>
<html lang="en">
<head>
<meta charset="utf-8">
<title>Maple Crest Holdings LLC — Letterhead</title>
<link rel="stylesheet" href="https://fonts.googleapis.com/css2?family=Crimson+Pro:wght@400&display=swap">
<style>
  :root {
    --paper: #ffffff;
    --page-edge: #b9b9b9;
    --ink: #3a3a3a;
    --brand-blue: #1f4e8c;
    --watermark: #ececec;
    --watermark-soft: #f4f4f4;
  }
  html, body {
    margin: 0;
    padding: 0;
    width: 928px;
    height: 1200px;
    overflow: hidden;
    background: var(--paper);
  }
  .letterhead {
    position: relative;
    box-sizing: border-box;
    width: 928px;
    height: 1200px;
    border: 1px solid var(--page-edge);
    background: var(--paper);
    font-family: "Crimson Pro", Georgia, serif;
  }
  .brand {
    position: absolute;
    left: 31px;
    top: 110px;
    margin: 0;
    font-size: 22px;
    font-weight: 400;
    font-variant: small-caps;
    letter-spacing: 0.6px;
    color: var(--brand-blue);
    line-height: 1;
  }
  .contact {
    position: absolute;
    left: 648px;
    top: 31px;
    margin: 0;
    font-style: normal;
    font-size: 15px;
    line-height: 17.5px;
    color: var(--ink);
    font-variant-numeric: oldstyle-nums;
  }
  .contact span { display: block; }
  .contact .web { color: var(--brand-blue); }
  .watermark-area {
    position: absolute;
    left: 55px;
    top: 400px;
    width: 815px;
    height: 460px;
  }
</style>
</head>
<body>
  <main class="letterhead">
    <p class="brand">Maple Crest Holdings llc</p>

    <address class="contact">
      <span>815 East Darrow Avenue, Suite 4B</span>
      <span>Chicago, Illinois 60417</span>
      <span>Office: 312-555-0148</span>
      <span>Facsimile: 312-555-0192</span>
      <span class="web">www.maplecrestholdingsllc.example</span>
      <span>info@maplecrestholdingsllc.example</span>
    </address>

    <svg class="watermark-area" viewBox="0 0 815 460" role="img" aria-label="Faint large brand emblem watermark area">
      <defs>
        <radialGradient id="watermark-fade" cx="50%" cy="55%" r="60%">
          <stop offset="0%" stop-color="var(--watermark)"/>
          <stop offset="100%" stop-color="var(--watermark-soft)" stop-opacity="0"/>
        </radialGradient>
      </defs>
      <rect x="0" y="0" width="815" height="460" rx="40" fill="url(#watermark-fade)"/>
    </svg>
  </main>
</body>
</html>
```